Carpet cleaning company focused on high quality needs business cards

We are a growing company that just merged with another company and need to design a new business card. We do both residential as well as commercial cleaning. We do carpet, tile & grout, upholstery, hard floors, and stain & pet odor removal. We treat our customers like family and strive to achieve outstanding results with every job.

```html
<!DOCTYPE html>
<html lang="en">
<head>
<meta charset="utf-8">
<title>Hearthway Steam Cleaning – Business Card</title>
<link href="https://fonts.googleapis.com/css2?family=Open+Sans:wght@400;600;700;800&display=swap" rel="stylesheet">
<style>
  :root {
    --backdrop: #bdbdbd;
    --card: #ffffff;
    --ink: #111111;
    --text: #222222;
    --accent: #e8463f;
    --shadow: rgba(0, 0, 0, 0.28);
  }
  * { box-sizing: border-box; margin: 0; padding: 0; }
  html, body { width: 1200px; height: 780px; overflow: hidden; }
  body {
    background: var(--backdrop);
    font-family: "Open Sans", Arial, sans-serif;
    color: var(--text);
    position: relative;
  }
  .card {
    position: absolute;
    top: 235px;
    width: 540px;
    height: 310px;
    background: var(--card);
    box-shadow: 0 8px 22px var(--shadow);
    overflow: hidden;
  }
  .card--front { left: 40px; }
  .card--back { left: 620px; }

  /* brand lockup: plain square + name in one weight */
  .brand { display: flex; align-items: center; gap: 14px; position: absolute; }
  .brand__square { background: var(--accent); flex: none; }
  .brand__name {
    font-weight: 800;
    color: var(--ink);
    line-height: 1.02;
    text-transform: uppercase;
  }
  .card--front .brand { left: 34px; top: 38px; }
  .card--front .brand__square { width: 62px; height: 62px; }
  .card--front .brand__name { font-size: 19px; }

  .card--back .brand { left: 50%; top: 50%; transform: translate(-50%, -50%); gap: 20px; }
  .card--back .brand__square { width: 110px; height: 110px; }
  .card--back .brand__name { font-size: 33px; }

  /* person */
  .person { position: absolute; right: 48px; top: 34px; text-align: right; }
  .person__name { font-size: 25px; font-weight: 700; line-height: 1.1; }
  .person__first { color: var(--accent); }
  .person__last { color: var(--ink); }
  .person__role { font-size: 13px; font-weight: 400; color: var(--ink); letter-spacing: 0.4px; margin-top: 2px; }
  .tab { position: absolute; right: 0; top: 34px; width: 30px; height: 28px; background: var(--accent); }

  /* address & contacts */
  .address {
    position: absolute; left: 34px; top: 136px;
    font-size: 14px; line-height: 1.45; color: var(--ink);
  }
  .contacts { position: absolute; left: 34px; bottom: 28px; list-style: none; }
  .contacts li {
    display: flex; align-items: center; gap: 10px;
    font-size: 14px; line-height: 1.6; color: var(--ink);
  }
  .contacts svg { width: 14px; height: 14px; flex: none; }
</style>
</head>
<body>

  <section class="card card--front" aria-label="Business card front">
    <div class="brand">
      <span class="brand__square"></span>
      <span class="brand__name">Hearthway<br>Steam Cleaning</span>
    </div>

    <div class="tab"></div>
    <div class="person">
      <p class="person__name"><span class="person__first">Marta</span> <span class="person__last">Kollar</span></p>
      <p class="person__role">Managing Director</p>
    </div>

    <p class="address">418 Linden Ave. Suite 120<br>Brookfield, TX 75410</p>

    <ul class="contacts">
      <li>
        <svg viewBox="0 0 16 16" aria-hidden="true"><path fill="var(--accent)" d="M4 1.5l2.2 3-1.3 1.6c.8 1.8 2.2 3.2 4 4l1.6-1.3 3 2.2-1.2 2.6C7 13.6 2.4 9 2 3.2z"/></svg>
        (555) 214-3087
      </li>
      <li>
        <svg viewBox="0 0 16 16" aria-hidden="true"><rect x="1" y="3" width="14" height="10" rx="1.5" fill="var(--accent)"/><path d="M2 4.5l6 4.5 6-4.5" fill="none" stroke="#fff" stroke-width="1.4"/></svg>
        hello@hearthwaysteam.com
      </li>
      <li>
        <svg viewBox="0 0 16 16" aria-hidden="true"><circle cx="8" cy="8" r="7" fill="var(--accent)"/><path d="M1 8h14M8 1c-3 3.5-3 10.5 0 14M8 1c3 3.5 3 10.5 0 14" fill="none" stroke="#fff" stroke-width="1"/></svg>
        www.hearthwaysteam.com
      </li>
    </ul>
  </section>

  <section class="card card--back" aria-label="Business card back">
    <div class="brand">
      <span class="brand__square"></span>
      <span class="brand__name">Hearthway<br>Steam Cleaning</span>
    </div>
  </section>

</body>
</html>
```